Dentistry Office

We want a new design for a Dentist's office website.

The theme is: "We provide high quality, state-of-the-art, dental care in a comfortable, caring environment."

The site currently has a menu on the left of the page with about 40 items on it. There is a great deal of textual content on each page, plus several illustrations.

We want to do this using CSS, so we need specifications in the CSS for all possible elements. The CSS needs to be named in a logical manner for easy use.

Every dentist on the planet seems to use lots of Flash. We don't want to because it is so distracting. We are looking for an elegant solution targeting 24-55 age group, but not excluding anyone.

The following (from another dentist's site) can give you a taste of what we want to communicate on the site:

"After 20 years of teaching dentists how to refine their technique and many years of writing textbooks, I currently devote my time to my office and the hands-on practice of dentistry. I'd like to welcome you personally to my dental practice, and I invite you to meet my highly experienced team of professionals.

"We have offered complete dental care of the highest quality since 1978. We provide Preventive Services, Tooth Whitening and Cosmetic Dentistry for a beautiful smile, Endodontics (root canal treatment) to treat painful teeth, Sedation Dentistry so you can relax, and Dental Implants to restore what is missing. We offer total care.

"Our approach to your health is simple: We use our education, experience and dedication to provide every patient with superior dental care.

"This passion for excellence is not just a goal, but a standard every member of our team holds.

"We also pride ourselves with our state of the art procedures, training and technology. This includes creating a beautiful smile using techniques that preserve as much of the original tooth as possible.

"Our abilities are renowned throughout the dental profession and I hope if you have any questions you will contact us by an e-mail note, by phone or just by dropping by."

Keep in mind the screen shape and dimensions. Your design needs to work in the normal screen proportions, regardless of how it looks when you post it here. Scrolling is OK, but the first impression needs to work.
Updates

Keep in mind that there will be about 250 words, or more, on each page.

Competitors web sites:

http://www.brindlecovedentist.example/

http://www.brindlecovedentalcare.example/

http://www.grinsbymarlowvaledental.example/

http://www.tenbyfamilydentalcare.example/

http://www.quelmardental.example/

http://www.dovrinadental.example/

We need to compete with these.

Target Market(s)

Generally adults seeking the most experienced and comfortable-to-be-with dentist.

Industry/Entity Type

Training

Requirements
Must have
• Must stand apart from other dentists.
• Must be elegant.
• Must have a horizontal menu structure across all columns, NOT a vertical that requires scrolling, no popout, pop down, etc. menus.
• We are looking for something special.
• Do not waste your time or ours putting up templates and things you have used before.
• Personally, I do not see how someone outside the US can understand the northern California dental market. But you are welcome to try.
Should not have
• Flash or graphics that move
• The look of a template
• Folksy fonts
• Looks like you used it 20 times before

```html
<!DOCTYPE html>
<html lang="en">
<head>
<meta charset="utf-8">
<title>Dentist's Office</title>
<link rel="stylesheet" href="https://fonts.googleapis.com/css2?family=Arimo:wght@400;700&family=Didact+Gothic&display=swap">
<style>
:root{
  --brand-blue:#1c6a9a;
  --brand-blue-dark:#155a86;
  --bar-blue:#1f72a5;
  --sky:#4fb3df;
  --ink:#3c3c3c;
  --ink-soft:#6b6b6b;
  --gold:#c9962e;
  --panel:#ffffff;
  --item-bg:#ececec;
  --item-line:#ffffff;
  --nav-active:#e9e9e9;
  --frame:#dcdcdc;
}
*{box-sizing:border-box;margin:0;padding:0}
html,body{width:1022px;height:1200px;overflow:hidden}
body{background:var(--brand-blue);font-family:"Arimo",Arial,sans-serif;color:var(--ink);position:relative}
.page{position:absolute;left:21px;top:26px;width:980px;height:1134px;background:var(--panel)}
.logo{position:absolute;left:38px;top:28px;display:flex;align-items:center;gap:10px}
.logo-dot{width:38px;height:38px;border-radius:50%;background:var(--sky)}
.logo-name{font-family:"Arimo",Arial,sans-serif;font-weight:700;font-size:26px;color:var(--brand-blue-dark)}
.call{position:absolute;right:15px;top:12px;font-size:21px;font-weight:700;color:var(--brand-blue-dark)}
.call span{color:var(--ink-soft);font-weight:400}

.sidebar{position:absolute;left:0;top:104px;width:208px}
.menu-group{margin-bottom:3px}
.menu-title{height:20px;background:var(--bar-blue);color:#fff;font-size:15px;text-align:center;line-height:20px}
.menu-item{height:18.3px;line-height:18px;background:var(--item-bg);border-bottom:1px solid var(--item-line);font-size:12px;padding-left:15px;color:#222}
.divider{position:absolute;left:212px;top:104px;width:2px;height:1030px;background:#e4e4e4}

.side-box{position:absolute;left:0;width:208px;background:var(--bar-blue);border-radius:9px;color:#fff;font-size:12.5px}
.side-box h3{font-weight:400;font-size:16px;text-align:center;padding-top:10px}
.quick{top:809px;height:149px}
.support{top:972px;height:150px}
.side-media{position:absolute;border-radius:4px}
.quick .side-media{left:6px;top:26px;width:90px;height:66px;background:linear-gradient(135deg,#3a4650,#9aa6ad)}
.support .side-media{left:14px;top:27px;width:66px;height:70px;background:linear-gradient(180deg,#e8d7c4,#f4f4f4 60%,#c9d5dd)}
.side-lines{position:absolute;left:105px;top:46px;line-height:20px}
.support .side-lines{left:105px;top:44px}
.side-foot{position:absolute;left:7px;bottom:22px;line-height:20px}
.support .side-foot{bottom:14px}

.hero{position:absolute;left:220px;top:101px;width:748px;height:262px;border:1px solid var(--frame);border-radius:10px;overflow:hidden;background:linear-gradient(90deg,#ffffff,#f3f3f3)}
.hero-photo{position:absolute;right:0;top:0;width:570px;height:100%;background:linear-gradient(90deg,rgba(255,255,255,0),#e6c3a6 22%,#7a5a44 45%,#e9cfb6 65%,#d9b47a 85%,#f3ead8)}
.hero-ask{position:absolute;left:8px;top:52px;font-size:19px;color:var(--gold)}
.hero-visit{position:absolute;left:75px;top:96px;font-size:21px;color:#444}

.nav{position:absolute;left:222px;top:370px;width:743px;height:45px;background:var(--bar-blue);display:flex;align-items:center;font-size:16.5px}
.nav a{color:#fff;text-decoration:none;height:100%;display:flex;align-items:center;padding:0 12px}
.nav a.active{background:var(--nav-active);color:#222;padding:0 14px;margin:0 8px}

.content{position:absolute;left:228px;top:428px;width:737px;height:682px;border-radius:18px;background:#fff;box-shadow:0 2px 9px rgba(0,0,0,.18)}
.content h1{position:absolute;left:39px;top:28px;font-family:"Didact Gothic","Arimo",sans-serif;font-weight:400;font-size:35px;color:var(--ink-soft)}
.content h1 strong{font-family:"Arimo",Arial,sans-serif;font-weight:700;color:var(--brand-blue-dark);font-size:31px}
.copy{position:absolute;left:45px;top:98px;width:680px;font-size:13.6px;line-height:22.5px;letter-spacing:.35px;color:#444}
.copy p{margin-bottom:7px}
.copy .gap{margin-top:32px}

.footer{position:absolute;left:0;top:1160px;width:1022px;height:40px;color:#fff;font-size:13.5px}
.footer .legal{position:absolute;left:41px;top:12px}
.footer .links{position:absolute;right:33px;top:12px;word-spacing:2px}
</style>
</head>
<body>
<div class="page">
  <div class="logo"><span class="logo-dot"></span><span class="logo-name">Dentist's Office</span></div>
  <div class="call">Call us: <span>000-000-0000</span></div>

  <nav class="sidebar">
    <div class="menu-group">
      <div class="menu-title">Education</div>
      <div class="menu-item">Emergency Dental Care</div>
      <div class="menu-item">Your Mouth</div>
      <div class="menu-item">Your Tooth</div>
      <div class="menu-item">Cracked Tooth?</div>
      <div class="menu-item">Missing a Tooth?</div>
      <div class="menu-item">Sensitive Teeth</div>
      <div class="menu-item">Dry Mouth</div>
      <div class="menu-item">Tooth Grinding</div>
      <div class="menu-item">Sleep Dentistry</div>
    </div>
    <div class="menu-group">
      <div class="menu-title">Preventative</div>
      <div class="menu-item">What is Preventive Care?</div>
      <div class="menu-item">Taking Care of Your Teeth</div>
      <div class="menu-item">Eating Right</div>
      <div class="menu-item">Dental Check-Ups</div>
      <div class="menu-item">Sealants</div>
      <div class="menu-item">Periodontal Disease</div>
      <div class="menu-item">Kicking the Habit</div>
      <div class="menu-item">Night Gurards</div>
    </div>
    <div class="menu-group">
      <div class="menu-title">Cosmetics</div>
      <div class="menu-item">Cosmetic Dentistry</div>
      <div class="menu-item">Bleaching and Whitening</div>
      <div class="menu-item">Cosmetic Bonding</div>
      <div class="menu-item">Esthetic Veneers</div>
      <div class="menu-item">Tooth Shaping</div>
    </div>
    <div class="menu-group">
      <div class="menu-title">Restorations</div>
      <div class="menu-item">Crowns/Caps:Each Step</div>
      <div class="menu-item">CMBRs</div>
      <div class="menu-item">Porcelain Bridges</div>
      <div class="menu-item">Bonded Dental Bridges</div>
      <div class="menu-item">Gold Restorations</div>
      <div class="menu-item">Implants</div>
    </div>
    <div class="menu-group">
      <div class="menu-title">Visiting our office</div>
      <div class="menu-item">Where to Stay</div>
      <div class="menu-item">First Visit / Map</div>
      <div class="menu-item">Financial Policy</div>
      <div class="menu-item">Dental Insurance</div>
    </div>
  </nav>
  <div class="divider"></div>

  <aside class="side-box quick">
    <h3>Our Quick Contact</h3>
    <div class="side-media" role="img" aria-label="Office desk telephone"></div>
    <div class="side-lines">Sample text<br>Sample text</div>
    <div class="side-foot">Sample text here Sample text here<br>Sample text here Sample text here</div>
  </aside>
  <aside class="side-box support">
    <h3>24 Hours Online Support</h3>
    <div class="side-media" role="img" aria-label="Support staff member portrait"></div>
    <div class="side-lines">Sample text<br>Sample text</div>
    <div class="side-foot">Sample text here Sample text here<br>Sample text here Sample text here</div>
  </aside>

  <section class="hero">
    <div class="hero-photo" role="img" aria-label="Two smiling women, patients of the practice"></div>
    <p class="hero-ask">Do you want a better looking Smile?</p>
    <p class="hero-visit">Visit our Office</p>
  </section>

  <nav class="nav">
    <a href="#">Home</a>
    <a href="#">Why we are Different</a>
    <a href="#" class="active">Technologies we offer</a>
    <a href="#">Meet Doctors</a>
    <a href="#">Our Team</a>
    <a href="#">Contact Us</a>
  </nav>

  <main class="content">
    <h1><strong>Welcome to</strong> Dentist office</h1>
    <div class="copy">
      <p>After 20 years of teaching dentists how to refine their technique and many years of writing textbooks,<br>&nbsp;I currently devote my time to my office and the hands-on practice of dentistry. to welcome you personally to my dental practice, and I invite you to meet my highly experienced team of professionals.</p>
      <p class="gap">We have offered complete dental care of the highest quality since 1978. We provide Preventive Services, Tooth Whitening and Cosmetic Dentistry for a beautiful smile,Endodontics (root canal treatment) to treat painful teeth, Sedation Dentistry so you can relax,and Dental Implants to restore what is missing.<br>We offer total care.</p>
      <p style="margin-top:14px">Our approach to your health is simple: We use our education, experience and dedication to provide every patient with superior dental care.</p>
      <p>This passion for excellence is not just a goal, but a standard every member of our team holds.</p>
      <p>We also pride ourselves with our state of the art procedures, training and technology. This includes creating a beautiful smile using techniques that preserve as much of the original tooth as possible.</p>
      <p style="margin-top:12px">Our abilities are renowned throughout the dental profession and I hope if you have any questions you will contact us by an e-mail note, by phone or just by dropping by.</p>
      <p style="margin-top:12px">We also pride ourselves with our state of the art procedures, training and technology. This includes creating a beautiful smile using techniques that preserve as much of the original tooth as possible.</p>
      <p style="margin-top:12px">We also pride ourselves with our state of the art procedures, training and technology. This includes creating a beautiful smile using techniques that preserve as much of the original tooth as possible.</p>
    </div>
  </main>
</div>

<footer class="footer">
  <span class="legal">copyright 2010&nbsp; Dentist office All rights reserved.</span>
  <span class="links">Home &nbsp;| &nbsp;Why we are Different &nbsp;| &nbsp;Technologies we offer &nbsp;| &nbsp;Meet Doctors &nbsp;| &nbsp;Out Team &nbsp;| &nbsp;Contact us</span>
</footer>
</body>
</html>
```